Business card for a new innovative and professional lawn care business

We need a business card design for a new lawn care business in Halifax NS Canada. We offer lawn services in Halifax & Bedford. Our services offered include lawn care, garden services, and property maintenance. We take pride in our work and are experienced at what we do. I would like to see a design that is double sided. On the backside I would like the something simple (maybe my logo preferably on blackround (linked below) with website link, Facebook page or something). The front I want to include contact info:
Morgan Pell
phone 902-555-0148
email - brookvaleyards.ca
facebook - Facebook.com/brookvaleyards
Instagram maybe ? - instagram.com/brookvaleyard
Serving Halifax and Bedford for 5 years?
I don't want it to have too much information as I will be passing them out in aim to visit website, or call !
We do want it to include lawn care, garden services and property maintenance.
Basic, catchy, and modern looking !
Logo attached below !

Target Market(s)

Passing business cards to everyone I meet or interact with.

Industry/Entity Type

Lawn Care

Contact Information for Business Card

Double sided with some basic information, with catchy colours and easy to look at.

Font styles to use
Sans Serif

Requirements
Must have
• Must be double sided and have :
• Name, Phone, Email, FB, Website, and 3 main services offered - lawn care, property maintenance, garden services
Nice to have
• Would be nice to have instagram link if it goes well on there
Should not have
• Don't want too much writing or images that are distracting

```html
<!DOCTYPE html>
<html lang="en">
<head>
<meta charset="utf-8">
<title>Brookvale Yards – Business Card</title>
<link href="https://fonts.googleapis.com/css2?family=Open+Sans:wght@400;600;800&display=swap" rel="stylesheet">
<style>
  :root{
    --bg:#ecebe6;
    --paper:#ffffff;
    --lime:#8dc63f;
    --forest:#0f6b35;
    --ink:#5a5a5a;
    --white:#ffffff;
  }
  *{box-sizing:border-box;margin:0;padding:0}
  html,body{width:1200px;height:950px;overflow:hidden}
  body{
    background:var(--bg);
    font-family:"Open Sans",Arial,sans-serif;
    display:flex;flex-direction:column;align-items:center;justify-content:center;gap:50px;
  }
  .card{
    position:relative;width:700px;height:400px;overflow:hidden;
    box-shadow:0 6px 18px rgba(0,0,0,.18);
  }
  .card-front{background:var(--paper)}
  .card-back{background:var(--lime)}
  .corner{position:absolute;inset:0;width:100%;height:100%}

  .brand{position:absolute;display:flex;align-items:center;gap:14px}
  .brand-dot{width:34px;height:34px;border-radius:50%;flex:none}
  .brand-name{
    display:flex;flex-direction:column;font-weight:800;letter-spacing:.04em;
    text-transform:uppercase;line-height:1.02;white-space:nowrap;
  }

  .card-front .brand{top:92px;left:320px}
  .card-front .brand-dot{background:var(--lime)}
  .card-front .brand-name{color:var(--forest);font-size:32px}

  .contact{position:absolute;left:56px;bottom:58px}
  .contact-name{
    color:var(--forest);font-weight:600;font-size:22px;letter-spacing:.22em;
    text-transform:uppercase;margin-bottom:12px;white-space:nowrap;
  }
  .contact-list{list-style:none}
  .contact-item{
    display:flex;align-items:center;gap:10px;color:var(--ink);font-size:15px;line-height:24px;white-space:nowrap;
  }
  .contact-icon{width:16px;height:16px;flex:none;display:flex;align-items:center;justify-content:center}
  .contact-icon .mark{width:14px;height:14px;border-radius:50%;background:var(--forest)}

  .card-back .brand{top:118px;left:50%;transform:translateX(-50%)}
  .card-back .brand-dot{background:var(--white);width:40px;height:40px}
  .card-back .brand-name{color:var(--white);font-size:44px}
  .services{
    position:absolute;left:0;right:0;top:262px;display:flex;justify-content:center;gap:22px;
    color:var(--white);font-size:17px;white-space:nowrap;
  }
  .service{display:flex;align-items:center;gap:8px}
  .service::before{content:"";width:8px;height:8px;border-radius:50%;background:var(--white);flex:none}
</style>
</head>
<body>

<section class="card card-front" aria-label="Card front">
  <svg class="corner" viewBox="0 0 700 400" aria-hidden="true">
    <path d="M540 0 Q690 10 700 170 L700 0 Z" fill="var(--forest)"/>
    <path d="M520 0 Q680 20 700 190" fill="none" stroke="var(--lime)" stroke-width="8"/>
    <path d="M0 230 Q20 390 200 400 L0 400 Z" fill="var(--lime)"/>
    <path d="M0 214 Q26 384 214 400" fill="none" stroke="var(--forest)" stroke-width="5"/>
  </svg>

  <div class="brand">
    <span class="brand-dot"></span>
    <span class="brand-name"><span>Brookvale</span><span>Yards</span></span>
  </div>

  <div class="contact">
    <p class="contact-name">Morgan Pell</p>
    <ul class="contact-list">
      <li class="contact-item">
        <span class="contact-icon">
          <svg width="14" height="14" viewBox="0 0 24 24"><path fill="var(--forest)" d="M6.6 10.8a15.1 15.1 0 0 0 6.6 6.6l2.2-2.2a1 1 0 0 1 1-.25 11.4 11.4 0 0 0 3.6.57 1 1 0 0 1 1 1V20a1 1 0 0 1-1 1A17 17 0 0 1 3 4a1 1 0 0 1 1-1h3.5a1 1 0 0 1 1 1c0 1.25.2 2.45.57 3.6a1 1 0 0 1-.25 1z"/></svg>
        </span>902-555-0148</li>
      <li class="contact-item"><span class="contact-icon"><span class="mark"></span></span>info@brookvaleyards.ca</li>
      <li class="contact-item"><span class="contact-icon"><span class="mark"></span></span>www.brookvaleyards.ca</li>
      <li class="contact-item"><span class="contact-icon"><span class="mark"></span></span>brookvaleyards</li>
      <li class="contact-item"><span class="contact-icon"><span class="mark"></span></span>brookvaleyard</li>
    </ul>
  </div>
</section>

<section class="card card-back" aria-label="Card back">
  <div class="brand">
    <span class="brand-dot"></span>
    <span class="brand-name"><span>Brookvale</span><span>Yards</span></span>
  </div>
  <div class="services">
    <span class="service">Lawn Care</span>
    <span class="service">Property Maintenance</span>
    <span class="service">Garden Services</span>
  </div>
</section>

</body>
</html>
```